Verdana Harvest Co - Business Card Design Project

We need business cards for our business. We grow roots and fruits in Central and South America, we import and distribute in FL, USA. We do fresh and frozen products.

Target Market(s)

Small and big supermarkets, wholesalers, traders, distributors, etc

Industry/Entity Type

Business

```html
<!DOCTYPE html>
<html lang="en">
<head>
<meta charset="utf-8">
<title>Verdana Harvest Co – Business Card</title>
<link rel="stylesheet" href="https://fonts.googleapis.com/css2?family=Questrial&display=swap">
<style>
  :root {
    --backdrop: #2b2b2b;
    --card: #f7f7f7;
    --card-edge: #e6e6e6;
    --brand-green: #5b6b35;
    --accent-orange: #e07b12;
    --ink: #3a3a3a;
    --rule: #8a8a8a;
  }
  * { box-sizing: border-box; margin: 0; padding: 0; }
  html, body {
    width: 1200px; height: 997px; overflow: hidden;
    background: var(--backdrop);
    font-family: "Questrial", "Century Gothic", sans-serif;
  }
  .canvas { position: relative; width: 1200px; height: 997px; }
  .card {
    position: absolute; width: 620px; height: 354px;
    background: linear-gradient(160deg, #ffffff 0%, var(--card) 60%, var(--card-edge) 100%);
    border-radius: 22px;
    box-shadow: 0 18px 40px rgba(0,0,0,.55);
  }
  .card--back { left: 110px; top: 90px; }
  .card--front { left: 470px; top: 520px; }

  .brand {
    position: absolute; display: flex; align-items: center; gap: 10px;
    color: var(--brand-green); font-size: 30px; letter-spacing: 1px; white-space: nowrap;
  }
  .brand__dot { width: 14px; height: 14px; border-radius: 50%; background: var(--brand-green); }
  .card--back .brand { right: 44px; bottom: 96px; }
  .card--front .brand { right: 40px; top: 44px; }

  .holder { position: absolute; left: 44px; top: 196px; }
  .holder__name { color: var(--accent-orange); font-size: 22px; letter-spacing: .5px; }
  .holder__role { color: var(--ink); font-size: 18px; margin-top: 2px; }

  .contacts { position: absolute; left: 44px; top: 262px; list-style: none; }
  .contacts li {
    display: flex; align-items: center; gap: 10px;
    color: var(--ink); font-size: 16px; line-height: 26px; white-space: nowrap;
  }
  .contacts svg { width: 15px; height: 15px; fill: var(--accent-orange); flex: none; }
  .web { position: absolute; left: 300px; top: 236px; display: flex; align-items: center; gap: 10px; color: var(--ink); font-size: 16px; }
  .web svg { width: 15px; height: 15px; stroke: var(--accent-orange); fill: none; stroke-width: 2.4; }
</style>
</head>
<body>
<main class="canvas">
  <section class="card card--back" aria-label="Card back">
    <div class="brand"><span class="brand__dot"></span>Verdana Harvest Co</div>
  </section>

  <section class="card card--front" aria-label="Card front">
    <div class="brand"><span class="brand__dot"></span>Verdana Harvest Co</div>

    <div class="holder">
      <p class="holder__name">YOUR NAME</p>
      <p class="holder__role">Designation</p>
    </div>

    <p class="web">
      <svg viewBox="0 0 16 16"><path d="M6.5 9.5l3-3M7 4.5l1.5-1.5a2.8 2.8 0 014 4L11 8.5M9 11.5L7.5 13a2.8 2.8 0 01-4-4L5 7.5"/></svg>
      www.harvestlinkfresh.net
    </p>

    <ul class="contacts">
      <li><svg viewBox="0 0 16 16"><path d="M3 2h3l1 3-2 1a8 8 0 005 5l1-2 3 1v3a1 1 0 01-1 1A13 13 0 012 3a1 1 0 011-1z"/></svg>+1 555-014-2290</li>
      <li><svg viewBox="0 0 16 16"><path d="M8 1.5l7 6.5h-2v6.5H9.5v-4h-3v4H3V8H1z"/></svg>72 Orchard Lane Dover, New Hampshire 03820</li>
      <li><svg viewBox="0 0 16 16"><path d="M1 3.5h14v9H1z M1.5 4l6.5 5 6.5-5" stroke="#fff" stroke-width="1"/></svg>orders@harvestlinkfresh.net</li>
    </ul>
  </section>
</main>
</body>
</html>
```